brightquokka.net we need a webpage designed for our new product

We need a webpage designed for our new range of products from our new brand. We have had a logo designed on sketchharbor (see attached) and we want to keep to this theme. Our first product is a range of affordable app controlled LED lightbulbs.

I have added some photos that we think is good inspirational material and would be good as a background to this website, but we want the site to look modern but not conventional. We would like something that makes our company look quirky not corporate.

Thats it

Target Market(s)

Our product is being stocked by big name online retailers in the UK, the page will get link through hits from our app. Our target market is gadget freaks of all ages.

Industry/Entity Type

It Company

Requirements
Must have
• We are going to need a help page, text to be uploaded next few days.

We need a contact page.

design my work on iOS and Android as most people will access page through their handset or tablet.
Should not have
• We do not want anything too corporate.

```html
<!DOCTYPE html>
<html lang="en">
<head>
<meta charset="utf-8">
<title>Bright Quokka – App Controlled LED Bulbs</title>
<link href="https://fonts.googleapis.com/css2?family=Open+Sans:wght@400;600;700&family=Oswald:wght@400;500&display=swap" rel="stylesheet">
<style>
:root{
  --green:#3aa935;
  --ink:#2b2b2b;
  --text:#555;
  --muted:#888;
  --line:#e2e2e2;
  --panel:#f2f2f2;
  --nav:#1f1f1f;
  --footer:#2a2a2a;
  --footer-base:#1a1a1a;
  --red:#d32222;
}
*{box-sizing:border-box;margin:0;padding:0}
html,body{width:802px;height:1200px;overflow:hidden}
body{font-family:"Open Sans",Arial,sans-serif;color:var(--text);background:#fff;position:relative;font-size:9px;line-height:1.45}
.wrap{position:absolute;left:75px;width:652px}

.site-header{position:absolute;top:0;left:0;width:802px;height:104px}
.brand{position:absolute;left:75px;top:30px;display:flex;align-items:center;gap:8px}
.brand-mark{width:26px;height:26px;background:var(--green)}
.brand-name{font-family:"Oswald",sans-serif;font-weight:500;font-size:17px;color:var(--green);letter-spacing:.5px}
.apply{position:absolute;right:75px;top:6px;background:var(--green);color:#fff;font-size:8px;padding:2px 9px}
.apply-left{right:128px}
.social{position:absolute;right:75px;top:32px;display:flex;gap:5px}
.social span{width:11px;height:11px;background:#444;border-radius:2px}
.call{position:absolute;right:75px;top:52px;font-family:"Oswald",sans-serif;font-size:20px;color:#333}

.main-nav{position:absolute;top:104px;left:75px;width:652px;height:22px;background:var(--nav);display:flex}
.main-nav a{color:#ddd;text-decoration:none;font-size:9px;padding:0 17px;line-height:22px}
.main-nav a.active{background:#3c3c3c;color:#fff}

.hero{position:absolute;top:126px;left:75px;width:652px;height:290px;background:radial-gradient(circle at 70% 35%,#e8b45a 0,#a4723f 30%,#4a3a33 70%,#2d2a33)}
.hero-caption{position:absolute;left:0;top:148px;width:285px;background:rgba(0,0,0,.72);padding:8px 12px 9px}
.hero-caption h1{font-family:"Oswald",sans-serif;font-weight:400;color:#fff;font-size:21px;line-height:1.2;margin-bottom:2px}
.hero-caption p{color:#ccc;font-size:8px;line-height:1.35}

.welcome{top:481px;height:68px;border:1px solid var(--line);border-left:4px solid var(--green);background:#fafafa;padding:7px 150px 0 12px}
.welcome h2{font-family:"Oswald",sans-serif;font-weight:400;font-size:18px;line-height:1.2;color:#333;margin-bottom:2px}
.welcome h2 b{color:var(--green);font-weight:400}
.welcome p{font-size:8px;color:var(--muted);line-height:1.3}
.btn{display:inline-block;background:#666;color:#fff;font-family:"Oswald",sans-serif;font-size:12px;padding:4px 14px}
.welcome .btn{position:absolute;right:14px;top:20px;background:#555}

.section-title{display:flex;align-items:center;gap:10px;height:30px;background:var(--panel);font-family:"Oswald",sans-serif;font-size:18px;color:#333;position:relative}
.section-title .icon{width:30px;height:30px;background:var(--green);display:flex;align-items:center;justify-content:center}
.products{top:598px}
.arrows{position:absolute;right:6px;top:9px;display:flex;gap:2px}
.arrows span{width:12px;height:12px;background:#bbb}
.product-row{display:flex;gap:17px;margin-top:18px}
.product{width:150px}
.product .photo{height:153px}
.product p{font-size:10px;color:#444;margin-top:12px}

.about{top:855px;width:440px}
.about p{margin-top:16px;font-size:8px;color:var(--muted);line-height:1.5}
.about .btn{margin-top:14px;font-family:"Open Sans",sans-serif;font-size:8px;padding:3px 10px;background:#555}

.contact{position:absolute;top:855px;left:540px;width:187px;height:162px;background:var(--panel)}
.contact .section-title{background:none}
.contact form{padding:10px 12px}
.field{height:15px;background:#fff;border:1px solid #ddd;margin-bottom:7px;font-size:7px;color:#aaa;padding:2px 5px}
.field.area{height:28px}
.submit{display:inline-block;background:#555;color:#fff;font-size:7px;padding:2px 8px}

.site-footer{position:absolute;top:1035px;left:75px;width:652px;height:140px;background:var(--footer);display:flex;padding-top:14px}
.col{width:163px;padding:0 12px;color:#aaa;font-size:8px}
.col h3{color:#fff;font-size:10px;font-weight:600;margin-bottom:7px}
.col ul{list-style:none}
.col li{line-height:1.5}
.col li.on{color:var(--green)}
.tel{display:flex;align-items:center;gap:5px;margin-top:6px}
.sub{display:flex;margin-top:8px}
.sub span{flex:1;height:12px;background:#fff}
.sub b{background:var(--red);color:#fff;font-size:7px;padding:0 6px;line-height:12px;font-weight:600}
.copyright{position:absolute;top:1175px;left:75px;width:652px;height:25px;background:var(--footer-base);color:#999;font-size:7px;text-align:center;line-height:22px}
</style>
</head>
<body>

<header class="site-header">
  <div class="brand"><span class="brand-mark"></span><span class="brand-name">BRIGHT QUOKKA</span></div>
  <span class="apply apply-left">Get the App</span>
  <span class="apply">Follow Now</span>
  <div class="social"><span></span><span></span><span></span><span></span><span></span><span></span></div>
  <div class="call">Call Now: 123-456-7890</div>
</header>

<nav class="main-nav">
  <a class="active">HOME</a><a>About Us</a><a>Product</a><a>Help</a><a>Contact Us</a>
</nav>

<section class="hero" role="img" aria-label="Photo of a room glowing in warm colours from smart LED bulbs">
  <div class="hero-caption">
    <h1>BRIGHT QUOKKA</h1>
    <p>Smart LED bulbs you boss around from your phone. Millions of colours, zero fuss, and a bill that won't make you cry.</p>
  </div>
</section>

<section class="wrap welcome">
  <h2>Welcome to <b>BRIGHT QUOKKA</b></h2>
  <p>We make affordable app controlled LED bulbs for gadget fans of all ages. Dim, colour, schedule and party-mode every room from your phone or tablet. No hub, no wiring, no boring bits. Find us at big online shops across the UK.</p>
  <span class="btn">READ MORE</span>
</section>

<section class="wrap products">
  <div class="section-title"><span class="icon"><svg width="14" height="14" viewBox="0 0 14 14"><rect x="2" y="4" width="10" height="8" fill="#fff"/><path d="M4 4V2h6v2" stroke="#fff" fill="none"/></svg></span>PRODUCTS
    <div class="arrows"><span></span><span></span></div>
  </div>
  <div class="product-row">
    <div class="product"><div class="photo" role="img" aria-label="Photo of the classic E27 colour bulb" style="background:linear-gradient(#6b4a3a,#e0a552)"></div><p>Glow Classic E27</p></div>
    <div class="product"><div class="photo" role="img" aria-label="Photo of an LED light strip kit" style="background:linear-gradient(#c44a8a,#d99a4a)"></div><p>Mood Strip Kit</p></div>
    <div class="product"><div class="photo" role="img" aria-label="Photo of a small candle bulb" style="background:linear-gradient(#7aa0c4,#e6d3b8)"></div><p>Candle Mini E14</p></div>
    <div class="product"><div class="photo" role="img" aria-label="Photo of a four bulb party pack" style="background:linear-gradient(#d9a23a,#6a4a2a)"></div><p>Party Pack of Four</p></div>
  </div>
</section>

<section class="wrap about">
  <div class="section-title"><span class="icon"><svg width="14" height="14" viewBox="0 0 14 14"><circle cx="7" cy="4" r="3" fill="#fff"/><path d="M1 13c0-4 12-4 12 0z" fill="#fff"/></svg></span>ABOUT US</div>
  <p>We are a tiny team of light nerds who got tired of expensive smart bulbs. So we built our own: bright, cheap and a bit cheeky. Pair a bulb in seconds, pick any colour, set a sunrise alarm or sync the lights to your music. Stuck? The Help page walks you through every step, from first screw-in to wild disco mode.</p>
  <span class="btn">Read More</span>
</section>

<section class="contact">
  <div class="section-title"><span class="icon"><svg width="14" height="14" viewBox="0 0 14 14"><path d="M3 1l3 3-2 2c1 2 2 3 4 4l2-2 3 3-2 2C6 13 1 8 1 3z" fill="#fff"/></svg></span>CONTACT US!</div>
  <form>
    <div class="field">Name</div>
    <div class="field">E-mail</div>
    <div class="field area">Message</div>
    <span class="submit">SUBMIT</span>
  </form>
</section>

<footer class="site-footer">
  <div class="col"><h3>About Us</h3><p>Affordable smart LED bulbs you run from one simple app. Made for tinkerers, gamers, grans and anyone who loves a good gadget.</p></div>
  <div class="col"><h3>Site Map</h3><ul><li class="on">Home</li><li>About Us</li><li>Product</li><li>Help</li><li>Contact Us</li></ul></div>
  <div class="col"><h3>Contact Us</h3><p>Bright Quokka, 12 Lamp Lane<br>Bristol, UK</p>
    <div class="tel"><svg width="9" height="9" viewBox="0 0 14 14"><path d="M3 1l3 3-2 2c1 2 2 3 4 4l2-2 3 3-2 2C6 13 1 8 1 3z" fill="#aaa"/></svg>123-456-7890</div></div>
  <div class="col"><h3>Infoletre</h3><p>Get new colour scenes, app updates and the odd silly light hack straight to your inbox.</p>
    <div class="sub"><span></span><b>Search</b></div></div>
</footer>
<div class="copyright">Copyright © 2014 brightquokka.net - All Rights Reserved</div>

</body>
</html>
```